Stylish business cards for KV7

To create an appealing and professional business card design for a WOMEN Owned Construction Supply Company.
2 sided card. Incorporate brand elements, curvy, colorful, sleek and bright. No solid white background. attached samples of styles added shapes/ribbons. Want something with that WOW that looks awesome, factor. It is a new logo, so feel free to mess with logo colors in the blue and teal factors that can look good with both dark and light background. If you want to try a watermark with just the KV7, without the "Supply" that might look cool to.

Industry/Entity Type

Women owned construction supply company

Contact Information for Business Card

Name, Title, and phone number and email, web page. maybe spot for qr code.

Font styles to use
Sans Serif

Requirements
Nice to have
• would love to see colors, maybe stylish ribbon dividers or some sort of 2 or 3 tone color card that compliments logo.
Should not have
• Please do not have all white background. Do not include Home/reale state/ or building images.

```html
<!DOCTYPE html>
<html lang="en">
<head>
<meta charset="UTF-8">
<title>KV7 Supply – Business Cards</title>
<link rel="stylesheet" href="https://fonts.googleapis.com/css2?family=Jost:wght@400;500;600&family=Great+Vibes&display=swap">
<style>
  :root {
    --navy-deep: #0b2747;
    --navy: #123a63;
    --teal: #1a86ad;
    --teal-bright: #2aa3cf;
    --silver-light: #f1f3f5;
    --silver-mid: #aeb6bd;
    --silver-dark: #7d878f;
    --paper: #ffffff;
    --text-light: #d9e8f2;
    --backdrop: #e9ecef;
  }
  * { box-sizing: border-box; margin: 0; padding: 0; }
  html, body {
    width: 1200px; height: 900px; overflow: hidden;
    background: var(--backdrop);
    font-family: "Jost", sans-serif;
  }
  .canvas {
    position: relative; width: 1200px; height: 900px;
  }
  .card {
    position: absolute; left: 280px;
    width: 640px; height: 366px;
    overflow: hidden;
    box-shadow: 0 14px 30px rgba(10, 30, 50, 0.28);
  }

  /* Back side */
  .card--back {
    top: 50px;
    border-radius: 30px;
    background: linear-gradient(90deg, var(--navy-deep) 0%, var(--navy) 30%, var(--teal) 55%, var(--navy) 80%, var(--navy-deep) 100%);
  }
  .card--back .pattern-field {
    position: absolute; inset: 0;
    background: linear-gradient(90deg, rgba(26,134,173,0.15), rgba(42,163,207,0.25) 55%, rgba(11,39,71,0.15));
  }
  .card--back .wordmark {
    position: absolute; right: 90px; top: 168px;
    font-size: 22px; font-weight: 500; color: var(--paper);
    letter-spacing: 0.5px;
  }

  /* Front side */
  .card--front {
    top: 480px;
    border-radius: 0 44px 0 44px;
    background: linear-gradient(135deg, var(--navy-deep) 0%, var(--navy) 45%, var(--teal) 100%);
  }
  .card--front .ribbons {
    position: absolute; inset: 0; width: 640px; height: 366px;
  }
  .card--front .wordmark {
    position: absolute; left: 420px; top: 90px;
    font-size: 44px; font-weight: 600; color: var(--navy);
    letter-spacing: 0.5px;
  }
  .contact {
    position: absolute; left: 40px; top: 120px;
    color: var(--text-light);
  }
  .contact__name {
    font-family: "Great Vibes", cursive;
    font-size: 38px; color: var(--navy-deep);
    line-height: 1;
    text-shadow: 0 0 1px rgba(255,255,255,0.2);
  }
  .contact__title {
    font-size: 14px; margin-top: 2px; letter-spacing: 0.3px;
  }
  .contact__rule {
    width: 240px; height: 1px; margin: 10px 0 10px;
    background: rgba(217, 232, 242, 0.55);
  }
  .contact__tagline { font-size: 15px; line-height: 1.3; padding-left: 10px; }
  .contact__lines { list-style: none; margin-top: 14px; padding-left: 10px; }
  .contact__lines li {
    display: flex; align-items: center; gap: 10px;
    font-size: 15px; line-height: 1.55;
  }
  .contact__lines svg { width: 14px; height: 14px; flex: none; }
</style>
</head>
<body>
<main class="canvas">

  <section class="card card--back" aria-label="Card back">
    <div class="pattern-field" role="img" aria-label="Repeating embossed brand-mark pattern in deep teal tones"></div>
    <span class="wordmark">KV7 Supply</span>
  </section>

  <section class="card card--front" aria-label="Card front">
    <svg class="ribbons" viewBox="0 0 640 366" aria-hidden="true">
      <defs>
        <linearGradient id="silver" x1="0" y1="0" x2="1" y2="1">
          <stop offset="0" stop-color="#7d878f"/>
          <stop offset="0.45" stop-color="#f1f3f5"/>
          <stop offset="1" stop-color="#aeb6bd"/>
        </linearGradient>
        <linearGradient id="tealband" x1="0" y1="0" x2="1" y2="1">
          <stop offset="0" stop-color="#2aa3cf"/>
          <stop offset="1" stop-color="#123a63"/>
        </linearGradient>
      </defs>
      <polygon points="230,0 330,0 640,300 640,366 610,366" fill="url(#silver)"/>
      <polygon points="250,40 300,40 630,366 560,366" fill="url(#tealband)"/>
      <polygon points="300,0 640,0 640,310" fill="#ffffff"/>
      <polygon points="300,0 345,0 640,290 640,310" fill="url(#silver)" opacity="0.9"/>
      <polygon points="345,0 640,0 640,290" fill="#fbfcfd"/>
    </svg>

    <span class="wordmark">KV7 Supply</span>

    <div class="contact">
      <p class="contact__name">Dana Whitfield</p>
      <p class="contact__title">Executive Director - Bus. Development</p>
      <div class="contact__rule"></div>
      <p class="contact__tagline">Vet &amp; Woman-Owned<br>TX &amp; Beyond</p>
      <ul class="contact__lines">
        <li>
          <svg viewBox="0 0 24 24"><path fill="currentColor" d="M6.6 10.8a15 15 0 0 0 6.6 6.6l2.2-2.2a1 1 0 0 1 1-.25 11.4 11.4 0 0 0 3.6.57 1 1 0 0 1 1 1V20a1 1 0 0 1-1 1A17 17 0 0 1 3 4a1 1 0 0 1 1-1h3.5a1 1 0 0 1 1 1c0 1.25.2 2.45.57 3.6a1 1 0 0 1-.25 1z"/></svg>
          (555) 014-2290
        </li>
        <li>
          <svg viewBox="0 0 24 24"><path fill="currentColor" d="M3 5h18v14H3zm2 2v.5l7 4.5 7-4.5V7zm0 2.8V17h14V9.8l-7 4.5z"/></svg>
          dw@kv7supply.com
        </li>
        <li>
          <svg viewBox="0 0 24 24"><circle cx="12" cy="12" r="9" fill="none" stroke="currentColor" stroke-width="2"/><path d="M3 12h18M12 3c3 3.5 3 14.5 0 18M12 3c-3 3.5-3 14.5 0 18" fill="none" stroke="currentColor" stroke-width="1.6"/></svg>
          www.kv7supply.com
        </li>
      </ul>
    </div>
  </section>

</main>
</body>
</html>
```